Landscaping flier 2024

Create a 1 page flier for landscaping services
1. Must be completed in Adobe Photoshop
2. Size 8.5" x 11" (portrait layout)
3. Include logo
4. Text to include:
2024 Gravesite Landscaping Packages
info@hollowbrookmemorial.org
(201) 555-0148
hollowbrookmemorial.org
5. Use chart text for the content. DO NOT COPY THE CHART DESIGN/FORMAT. Use the chart for the text you need only.
6. Use "Pricing cards as format for laying out the chart". Open to other ideas as well.
**Use the example of chart design (handwritten) to base your design off of.
7. Photos
-include before and after care photos

```html
<!DOCTYPE html>
<html lang="en">
<head>
<meta charset="utf-8">
<title>2024 Gravesite Landscaping Packages</title>
<link rel="stylesheet" href="https://fonts.googleapis.com/css2?family=Oswald:wght@600&family=Poppins:wght@400;500;600;700;800&display=swap">
<style>
  :root {
    --maroon: #7a1f2b;
    --maroon-dark: #5e1520;
    --pink: #fbdde0;
    --row-gray: #efefef;
    --white: #ffffff;
    --ink: #2a2a2a;
    --tick: #2fb36b;
    --cross: #e04a4a;
    --page-bg: #e9e9ea;
  }
  * { box-sizing: border-box; margin: 0; padding: 0; }
  html, body { width: 1200px; height: 2362px; overflow: hidden; background: var(--page-bg); }
  body { position: relative; font-family: "Poppins", sans-serif; color: var(--ink); }

  .flier {
    position: absolute; left: 50px; top: 470px;
    width: 914px; height: 1182px;
    transform: scale(1.2035); transform-origin: top left;
    background: var(--white); overflow: hidden;
    box-shadow: 0 6px 20px rgba(0,0,0,.15);
  }
  .abs { position: absolute; }
  .backdrop { position: absolute; left: 0; top: 0; }

  .brand {
    left: 0; right: 0; top: 70px; display: flex; justify-content: center; align-items: center; gap: 12px;
    color: var(--maroon); font-weight: 500; font-size: 27px; letter-spacing: .5px;
  }
  .brand-dot { width: 34px; height: 34px; border-radius: 50%; background: var(--maroon); }

  .year {
    left: 118px; top: 184px; font-family: "Oswald", sans-serif; font-weight: 600;
    font-size: 156px; line-height: 1; color: var(--white); letter-spacing: -3px;
    white-space: nowrap;
  }
  .title-line { left: 441px; color: var(--white); font-weight: 800; line-height: 1; white-space: nowrap; }
  .title-1 { top: 192px; font-size: 59px; }
  .title-2 { top: 248px; font-size: 47px; }
  .title-bar {
    left: 441px; top: 300px; width: 352px; height: 38px; background: var(--maroon);
    color: var(--white); font-size: 30px; font-weight: 500; letter-spacing: 14px;
    display: flex; align-items: center; padding-left: 26px;
  }

  .card {
    position: absolute; top: 380px; height: 585px;
    border: 3px solid var(--maroon); border-radius: 18px; overflow: hidden;
    background: var(--white); display: flex; flex-direction: column;
  }
  .card-seasonal { left: 55px; width: 250px; }
  .card-basic { left: 332px; width: 245px; }
  .card-perpetual { left: 608px; width: 250px; }

  .card-head {
    height: 72px; background: var(--maroon); color: var(--white);
    font-weight: 700; font-size: 17px; line-height: 1.2; text-align: center;
    display: flex; align-items: center; justify-content: center; position: relative;
  }
  .card-perpetual .card-head { padding-top: 12px; }
  .ribbon {
    position: absolute; right: -36px; top: 6px; transform: rotate(24deg);
    background: var(--pink); color: var(--maroon); font-size: 9.5px; font-weight: 700;
    padding: 1px 30px; text-transform: uppercase; line-height: 1.3; white-space: nowrap;
  }
  .card-desc {
    height: 72px; background: var(--row-gray); font-size: 13px; line-height: 1.25;
    display: flex; align-items: center; justify-content: center; text-align: center; padding: 0 14px;
  }
  .feature {
    display: flex; flex-direction: column; justify-content: center; padding: 0 12px 0 16px;
    font-size: 12.5px; font-weight: 500; text-transform: uppercase; line-height: 1.25;
  }
  .feature-row { display: flex; align-items: flex-start; gap: 10px; }
  .feature-row svg { flex: none; width: 15px; height: 15px; margin-top: 1px; }
  .feature-note { text-transform: none; font-weight: 400; font-size: 12px; text-align: center; margin-top: 4px; line-height: 1.2; white-space: nowrap; }
  .h-weed { height: 88px; background: var(--white); }
  .h-mon { height: 47px; background: var(--row-gray); }
  .h-pay { height: 50px; background: var(--white); }
  .h-box { height: 53px; background: var(--row-gray); }
  .h-rep { height: 47px; background: var(--white); }
  .h-trust { height: 47px; background: var(--row-gray); }

  .card-price {
    flex: 1; background: var(--pink); border-top: 3px solid var(--maroon);
    display: flex; flex-direction: column; align-items: center; justify-content: center; text-align: center;
  }
  .price-lead { font-size: 15px; }
  .price-amount { font-size: 28px; font-weight: 700; color: var(--maroon); line-height: 1.15; }
  .price-note { font-size: 11.5px; }
  .term-list { display: flex; gap: 6px; margin-bottom: 8px; }
  .term { width: 68px; border: 1.5px solid var(--maroon); border-radius: 5px; overflow: hidden; font-size: 12.5px; line-height: 1.2; }
  .term-years { background: var(--maroon); color: var(--white); font-weight: 500; }
  .term-cost { background: var(--white); }
  .term-caption { font-size: 12px; line-height: 1.2; }

  .proof {
    position: absolute; top: 998px; height: 148px; width: 240px;
    display: flex; border-radius: 4px; overflow: hidden;
  }
  .proof-before { left: 57px; }
  .proof-after { left: 309px; }
  .proof-label {
    width: 30px; background: #1e1e1e; color: var(--white); font-size: 13px; font-weight: 700;
    writing-mode: vertical-rl; transform: rotate(180deg); display: flex; align-items: center; justify-content: center;
  }
  .proof-photo { flex: 1; }
  .proof-before .proof-photo { background: linear-gradient(180deg, #8d9a88 0%, #6d9a45 40%, #4f8a2c 100%); }
  .proof-after .proof-photo { background: linear-gradient(180deg, #9aa49a 0%, #73a04a 40%, #3f7a28 100%); }

  .footer-band { left: 0; top: 1102px; width: 914px; height: 80px; background: var(--maroon); }
  .call { left: 565px; top: 1006px; font-size: 23px; font-weight: 800; color: var(--maroon); white-space: nowrap; }
  .call span { color: #1f1f1f; font-weight: 700; }
  .contact { left: 566px; font-size: 13.5px; display: flex; align-items: center; gap: 9px; white-space: nowrap; }
  .contact svg { width: 11px; height: 11px; }
  .contact-mail { top: 1038px; }
  .contact-addr { top: 1062px; }
  .website { left: 567px; top: 1116px; color: var(--white); font-size: 19px; font-weight: 500; letter-spacing: 1px; white-space: nowrap; }
</style>
</head>
<body>
<main class="flier">
  <svg class="backdrop" width="914" height="1182" viewBox="0 0 914 1182" role="img" aria-label="Autumn foliage of red and orange trees behind the header">
    <defs>
      <linearGradient id="foliage" x1="0" y1="0" x2="1" y2="1">
        <stop offset="0" stop-color="#8c3a2a"/>
        <stop offset=".4" stop-color="#b0553a"/>
        <stop offset=".7" stop-color="#9a3b35"/>
        <stop offset="1" stop-color="#7a2a2e"/>
      </linearGradient>
    </defs>
    <polygon points="0,0 90,0 215,153 700,153 825,0 914,0 914,440 850,495 64,495 0,440" fill="url(#foliage)"/>
  </svg>

  <div class="abs brand"><span>Hollowbrook</span><span class="brand-dot"></span><span>Memorial</span></div>

  <div class="abs year">2024</div>
  <div class="abs title-line title-1">GRAVESITE</div>
  <div class="abs title-line title-2">LANDSCAPING</div>
  <div class="abs title-bar">PACKAGES</div>

  <svg width="0" height="0" style="position:absolute">
    <symbol id="icon-yes" viewBox="0 0 16 16"><circle cx="8" cy="8" r="8" fill="#2fb36b"/><path d="M4.5 8.3l2.3 2.3 4.7-4.8" fill="none" stroke="#fff" stroke-width="2" stroke-linecap="round" stroke-linejoin="round"/></symbol>
    <symbol id="icon-no" viewBox="0 0 16 16"><circle cx="8" cy="8" r="8" fill="#e04a4a"/><path d="M5.3 5.3l5.4 5.4M10.7 5.3l-5.4 5.4" stroke="#fff" stroke-width="1.9" stroke-linecap="round"/></symbol>
  </svg>

  <section class="card card-seasonal">
    <div class="card-head">SEASONAL<br>CARE</div>
    <div class="card-desc">Seasonal<br>landscaping care.</div>
    <div class="feature h-weed"><div class="feature-row"><svg><use href="#icon-yes"/></svg>Weeding &amp; Trimming</div><div class="feature-note">Approximately every 7 weeks<br>during the growing season :<br>mid-April through mid-October</div></div>
    <div class="feature h-mon"><div class="feature-row"><svg><use href="#icon-no"/></svg>Monument Leveling</div></div>
    <div class="feature h-pay"><div class="feature-row"><svg><use href="#icon-no"/></svg>Payment ensures grave<br>care forever</div></div>
    <div class="feature h-box"><div class="feature-row"><svg><use href="#icon-no"/></svg>Full bed of boxwood<br>shrubs</div></div>
    <div class="feature h-rep"><div class="feature-row"><svg><use href="#icon-no"/></svg>Replacement of shrubs</div></div>
    <div class="feature h-trust"><div class="feature-row"><svg><use href="#icon-no"/></svg>Trust certificate</div></div>
    <div class="card-price">
      <div class="term-list">
        <div class="term"><div class="term-years">3 Years</div><div class="term-cost">$396</div></div>
        <div class="term"><div class="term-years">2 Years</div><div class="term-cost">$264</div></div>
        <div class="term"><div class="term-years">1 Years</div><div class="term-cost">$132</div></div>
      </div>
      <div class="term-caption">Multi-year payment<br>locks in current rates</div>
    </div>
  </section>

  <section class="card card-basic">
    <div class="card-head">BASIC CARE<br>ENDOWMENT</div>
    <div class="card-desc">Landscaping care forever for graves with no plantings.</div>
    <div class="feature h-weed"><div class="feature-row"><svg><use href="#icon-yes"/></svg>Weeding &amp; Trimming</div><div class="feature-note">2 times per year :<br>mid-May &amp;<br>mid-September</div></div>
    <div class="feature h-mon"><div class="feature-row"><svg><use href="#icon-yes"/></svg>Monument Leveling</div></div>
    <div class="feature h-pay"><div class="feature-row"><svg><use href="#icon-yes"/></svg>Payment ensures grave<br>care forever</div></div>
    <div class="feature h-box"><div class="feature-row"><svg><use href="#icon-no"/></svg>Full bed of boxwood<br>shrubs</div></div>
    <div class="feature h-rep"><div class="feature-row"><svg><use href="#icon-no"/></svg>Replacement of shrubs</div></div>
    <div class="feature h-trust"><div class="feature-row"><svg><use href="#icon-no"/></svg>Trust certificate</div></div>
    <div class="card-price">
      <div class="price-lead">12 monthly payments of</div>
      <div class="price-amount">$287</div>
      <div class="price-note">Call for single payment discount.</div>
    </div>
  </section>

  <section class="card card-perpetual">
    <div class="card-head">PERPETUAL CARE<br>ENDOWMENT<span class="ribbon">Most popular</span></div>
    <div class="card-desc">Landscaping care forever for graves with plantings.</div>
    <div class="feature h-weed"><div class="feature-row"><svg><use href="#icon-yes"/></svg>Weeding &amp; Trimming</div><div class="feature-note">Approximately every 7 weeks<br>during the growing season :<br>mid-April through mid-October</div></div>
    <div class="feature h-mon"><div class="feature-row"><svg><use href="#icon-yes"/></svg>Monument Leveling</div></div>
    <div class="feature h-pay"><div class="feature-row"><svg><use href="#icon-yes"/></svg>Payment ensures grave<br>care forever</div></div>
    <div class="feature h-box"><div class="feature-row"><svg><use href="#icon-yes"/></svg>Full bed of boxwood<br>shrubs</div></div>
    <div class="feature h-rep"><div class="feature-row"><svg><use href="#icon-yes"/></svg>Replacement of shrubs</div></div>
    <div class="feature h-trust"><div class="feature-row"><svg><use href="#icon-yes"/></svg>Trust certificate</div></div>
    <div class="card-price">
      <div class="price-lead">12 monthly payments of</div>
      <div class="price-amount">$351</div>
      <div class="price-note">Call for single payment discount.</div>
    </div>
  </section>

  <div class="abs footer-band"></div>

  <div class="proof proof-before">
    <div class="proof-label">BEFORE CARE</div>
    <div class="proof-photo" role="img" aria-label="Gravesite with overgrown shrub before care"></div>
  </div>
  <div class="proof proof-after">
    <div class="proof-label">AFTER CARE</div>
    <div class="proof-photo" role="img" aria-label="Gravesite with neatly trimmed boxwood bed after care"></div>
  </div>

  <div class="abs call">CALL US: <span>201-555-0148</span></div>
  <div class="abs contact contact-mail"><svg viewBox="0 0 12 12"><rect x="0.5" y="2" width="11" height="8" rx="1" fill="#7a1f2b"/><path d="M1 2.5l5 4 5-4" fill="none" stroke="#fff" stroke-width="1"/></svg>info@hollowbrookmemorial.org</div>
  <div class="abs contact contact-addr"><svg viewBox="0 0 12 12"><path d="M6 0.5a3.5 3.5 0 0 0-3.5 3.5c0 2.6 3.5 6 3.5 6s3.5-3.4 3.5-6A3.5 3.5 0 0 0 6 0.5z" fill="#7a1f2b"/><circle cx="6" cy="4" r="1.3" fill="#fff"/><rect x="1.5" y="10.5" width="9" height="1" fill="#7a1f2b"/></svg>48 Alder Lane Fairview, NJ 07022</div>
  <div class="abs website">www.hollowbrookmemorial.org</div>
</main>
</body>
</html>
```